Private Investment Firm Needs PowerPoint Presentation Template

Design PowerPoint template, take Pinebrook-submitted rough presentation draft, and drop it into new template. See attached Project Brief file for more detail.
Updates

Some decent designs have been submitted but they seem to lack the understanding of our target markets. I am hopeful that more time and feedback will result in better results.

Target Market(s)

Private company owners and intermediaries.

Font styles to use
Serif

Colors
3176b5

Requirements
Must have
• See attached Project Brief.
Nice to have
Should not have
• No B2C fluff--this is a B2B project.

```html
<!DOCTYPE html>
<html lang="en">
<head>
<meta charset="utf-8">
<title>Pinebrook Capital – Introduction to Non-Control Capital</title>
<link href="https://fonts.googleapis.com/css2?family=Roboto+Condensed:wght@400;700&family=Roboto:wght@400;700&family=Merriweather:wght@700&display=swap" rel="stylesheet">
<style>
:root{
  --navy:#1b3a66;
  --blue:#3176b5;
  --sky:#6fa6d8;
  --pale:#e8f0f8;
  --ink:#2b2b2b;
  --grey:#8a8f96;
  --bg:#ffffff;
}
*{box-sizing:border-box;margin:0;padding:0}
html,body{width:839px;height:1200px;overflow:hidden;background:var(--bg)}
body{position:relative;font-family:"Roboto",Arial,sans-serif;color:var(--ink)}
.slide{position:absolute;background:#fff;border:1px solid #d5dbe3;overflow:hidden}
.col-l{left:6px;width:410px}
.col-r{left:423px;width:410px}
.photo{position:absolute;background:linear-gradient(135deg,#9cc2e6 0%,#3f79b0 45%,#173257 100%)}
.photo.grey{background:linear-gradient(135deg,#cfd3d8,#7d848c 60%,#4d545c)}
.brand{font-family:"Merriweather",Georgia,serif;font-weight:700;color:var(--navy);font-size:10px;letter-spacing:1px;display:flex;align-items:center;gap:5px}
.brand .mark{width:9px;height:9px;background:var(--blue);border-radius:50%}
.brand small{display:block;font-size:6px;letter-spacing:2px;color:var(--blue)}
.heading{font-family:"Roboto Condensed",Arial,sans-serif;font-weight:700;color:var(--navy);text-transform:uppercase;line-height:1.05}
.bar{position:absolute;left:0;top:0;height:100%;width:6px;background:var(--blue)}
.body{font-size:6.2px;line-height:1.5}
.body li{margin:0 0 4px 9px}
.body li::marker{color:var(--blue)}
.numlist{list-style:none;counter-reset:n;font-size:5.8px;line-height:1.4}
.numlist li{counter-increment:n;position:relative;padding-left:14px;margin-bottom:3.5px}
.numlist li::before{content:counter(n);position:absolute;left:0;top:0;width:9px;height:9px;background:var(--blue);color:#fff;font-size:5.5px;font-weight:700;text-align:center;line-height:9px}
.numlist b{color:var(--navy)}
.quote{position:absolute;left:0;right:0;text-align:center;color:#fff;font-family:"Roboto Condensed",Arial,sans-serif;font-weight:700;text-transform:uppercase;font-size:9.5px;line-height:1.35;padding:0 34px}
.person{position:absolute;width:52px;height:52px;border-radius:50%;border:2px solid #fff}
.sig{position:absolute;color:#fff;font-size:7px;line-height:1.4}
.sig b{font-size:9px;font-family:"Roboto Condensed",Arial,sans-serif}
table{border-collapse:collapse;width:100%;font-size:6px}
td,th{border:1px solid #c8d3e0;padding:2.5px 4px;text-align:left}
th{background:var(--navy);color:#fff;font-weight:700}
.hl td{background:var(--pale);font-weight:700;color:var(--navy)}
.stack{display:flex;flex-direction:column;gap:2px}
.stack div{color:#fff;font-size:6.5px;font-weight:700;padding:0 8px;display:flex;align-items:center}
</style>
</head>
<body>

<!-- Title slide -->
<section class="slide col-l" style="top:4px;height:228px">
  <div class="photo" style="left:150px;top:0;width:260px;height:228px" role="img" aria-label="Upward view of glass office towers in blue tones"></div>
  <svg width="410" height="228" style="position:absolute;left:0;top:0">
    <polygon points="0,0 210,0 150,228 0,228" fill="#fff"/>
    <polygon points="210,0 222,0 162,228 150,228" fill="#3176b5"/>
  </svg>
  <div class="brand" style="position:absolute;left:16px;top:16px"><span class="mark"></span><span>PINEBROOK<small>CAPITAL</small></span></div>
  <div class="heading" style="position:absolute;left:16px;top:70px;font-size:21px;width:170px">Introduction<br>to Non-Control<br>Capital</div>
  <div class="body" style="position:absolute;left:16px;top:142px;width:150px;color:var(--grey)">The Lower Middle Market Private Company Strategy for Raising Capital While Maintaining Business Control</div>
  <div style="position:absolute;left:16px;bottom:14px;font-size:6px;color:var(--grey)">June 2024</div>
</section>

<!-- Introduction -->
<section class="slide col-l" style="top:240px;height:102px">
  <div class="bar"></div>
  <div class="photo" style="right:0;top:0;width:120px;height:34px" role="img" aria-label="Office buildings photograph"></div>
  <div class="heading" style="position:absolute;left:16px;top:12px;font-size:13px">Introduction</div>
  <ul class="body" style="position:absolute;left:16px;top:36px;width:370px">
    <li>Private company owners have traditionally considered two capital-raising options: selling a business or borrowing more debt.</li>
    <li>An alternative: raise non-control capital that keeps the owner in charge of strategy and daily operations while adding growth funds.</li>
    <li>This overview explains when the approach fits and how it compares.</li>
  </ul>
</section>

<!-- What is non-control capital -->
<section class="slide col-r" style="top:4px;height:338px">
  <div class="bar"></div>
  <div class="heading" style="position:absolute;left:16px;top:12px;font-size:13px">What is Non-Control Capital?</div>
  <ul class="body" style="position:absolute;left:16px;top:32px;width:380px">
    <li>Non-control capital is an investment in which a partner provides funding while the owner keeps voting control.</li>
    <li>It is typically structured as subordinated debt, preferred equity, or a combination.</li>
    <li>Owners keep operational authority and retain most of the future upside.</li>
    <li>Regular reporting and board observation rights help align both parties.</li>
  </ul>
  <div class="heading" style="position:absolute;right:16px;top:118px;font-size:12px;text-align:right;color:var(--blue)">When is a<br>Non-Control Transaction Appropriate?</div>
  <ul class="body" style="position:absolute;left:16px;top:150px;width:380px">
    <li>The business has stable cash flow and a clear plan for growth.</li>
    <li>Owners want liquidity but are not ready to sell the company.</li>
    <li>Family members seek to buy out shareholders or partners.</li>
    <li>Senior lenders have reached their limit and more capital is needed.</li>
    <li>A management team wants to finance an acquisition or expansion.</li>
    <li>The owner values flexibility over the lowest possible cost of capital.</li>
    <li>Timing matters and a sale process would distract the team.</li>
  </ul>
</section>

<!-- Quote blue -->
<section class="slide col-l" style="top:350px;height:232px">
  <div class="photo" style="left:0;top:0;width:410px;height:232px" role="img" aria-label="Blue-toned city skyline background"></div>
  <div class="quote" style="top:52px">“Our company had several business opportunities but I needed outside capital to take advantage of them. Non-control capital let me grow without giving up the business I built.”</div>
  <div class="person" style="left:150px;top:150px;background:linear-gradient(#c9d6e4,#6b87a6)" role="img" aria-label="Portrait of the client executive"></div>
  <div class="sig" style="left:210px;top:162px"><b>Daniel Mercer</b><br>CEO<br>Harbor Ridge Group</div>
</section>

<!-- Quote grey -->
<section class="slide col-r" style="top:350px;height:232px">
  <div class="photo grey" style="left:0;top:0;width:410px;height:232px" role="img" aria-label="Grey-toned office interior background"></div>
  <div class="quote" style="top:52px">“Our company had several business opportunities but I needed outside capital to take advantage of them. Non-control capital let me grow without giving up the business I built.”</div>
  <div class="person" style="left:150px;top:150px;background:linear-gradient(#dadada,#777)" role="img" aria-label="Portrait of the client executive"></div>
  <div class="sig" style="left:210px;top:162px"><b>Daniel Mercer</b><br>CEO<br>Harbor Ridge Group</div>
</section>

<!-- 12 uses (1) -->
<section class="slide col-l" style="top:590px;height:236px">
  <div class="bar"></div>
  <div class="heading" style="position:absolute;left:16px;top:12px;font-size:12px">The 12 Primary Uses of Non-Control Capital</div>
  <ol class="numlist" style="position:absolute;left:16px;top:34px;width:380px">
    <li><b>Growth</b> – fund new products, markets, plants or sales teams.</li>
    <li><b>Acquisitions</b> – buy a competitor, supplier or complementary business.</li>
    <li><b>Partner Buyouts</b> – purchase the shares of a departing partner.</li>
    <li><b>Management Buyouts</b> – help managers gain ownership over time.</li>
    <li><b>Recapitalizations</b> – rebalance debt and equity on the balance sheet.</li>
    <li><b>Owner Liquidity</b> – take some value off the table while keeping control.</li>
    <li><b>Family Transitions</b> – move the business to the next generation.</li>
  </ol>
</section>

<!-- 12 uses (2) -->
<section class="slide col-r" style="top:590px;height:236px">
  <div class="bar"></div>
  <div class="heading" style="position:absolute;left:16px;top:12px;font-size:12px">The 12 Primary Uses of Non-Control Capital</div>
  <ol class="numlist" start="8" style="position:absolute;left:16px;top:34px;width:380px;counter-reset:n 7">
    <li><b>Refinancing</b> – replace expensive or restrictive existing debt.</li>
    <li><b>Turnaround Support</b> – strengthen a company after a tough period.</li>
    <li><b>Working Capital</b> – support larger contracts and inventory needs.</li>
    <li><b>Capital Projects</b> – finance equipment and facility upgrades.</li>
    <li><b>Estate Planning</b> – prepare ownership for tax and succession goals.</li>
  </ol>
</section>

<!-- Junior capital -->
<section class="slide col-l" style="top:834px;height:360px">
  <div class="bar"></div>
  <div class="heading" style="position:absolute;left:16px;top:12px;font-size:12px">Pinebrook Provides Junior Capital</div>
  <div style="position:absolute;left:16px;top:34px;width:378px">
    <table>
      <tr><th colspan="2">Balance Sheet Example</th></tr>
      <tr><td>Cash &amp; Receivables</td><td>Senior Debt – Bank</td></tr>
      <tr><td>Inventory</td><td>Revolving Credit Line</td></tr>
      <tr class="hl"><td>Equipment</td><td>Junior Capital – Pinebrook</td></tr>
      <tr><td>Real Estate</td><td>Owner Equity</td></tr>
      <tr><td>Goodwill</td><td>Retained Earnings</td></tr>
    </table>
    <div class="heading" style="font-size:9px;margin:12px 0 5px;color:var(--blue)">What Pinebrook Invests</div>
    <ul class="body">
      <li>Investments typically range from $3 million to $15 million per company.</li>
      <li>Subordinated debt with modest equity participation.</li>
      <li>Patient capital with flexible repayment schedules.</li>
      <li>A board seat or observer role, never operating control.</li>
    </ul>
  </div>
</section>

<!-- Balance sheet stack -->
<section class="slide col-r" style="top:834px;height:360px">
  <div class="bar"></div>
  <div class="heading" style="position:absolute;left:16px;top:12px;font-size:12px">Balance Sheet</div>
  <div style="position:absolute;left:16px;top:28px;font-size:8px;color:var(--blue);font-weight:700">Pinebrook's Position in the Capital Stack</div>
  <div class="stack" style="position:absolute;left:16px;top:50px;width:378px">
    <div style="height:40px;background:var(--navy)">Senior Debt – lowest risk, lowest cost</div>
    <div style="height:34px;background:#244c82">Asset-Based Lending</div>
    <div style="height:44px;background:var(--blue)">Junior Capital – Pinebrook</div>
    <div style="height:34px;background:var(--sky)">Preferred Equity</div>
    <div style="height:40px;background:#a9c8e6;color:var(--navy)">Common Equity – highest risk, highest return</div>
  </div>
  <svg width="20" height="200" style="position:absolute;left:376px;top:50px" aria-hidden="true">
    <line x1="10" y1="198" x2="10" y2="8" stroke="#1b3a66" stroke-width="1.5"/>
    <polygon points="5,10 10,0 15,10" fill="#1b3a66"/>
  </svg>
  <div class="body" style="position:absolute;left:16px;top:262px;width:378px;color:var(--grey)">Junior capital sits between senior lenders and equity holders, giving owners added funding without selling control of the company.</div>
</section>

</body>
</html>
```